Firm Stationery Design

I need a design for stationery, including: Stationery First Page, Stationery Second Sheet, Envelope, Mailing Label for Flat Envelopes, and Business Cards

```html
<!DOCTYPE html>
<html lang="en">
<head>
<meta charset="utf-8">
<title>Harlow Law LLC – Stationery</title>
<link rel="stylesheet" href="https://fonts.googleapis.com/css2?family=Montserrat:wght@600&family=Roboto:wght@300;400;500;700&display=swap">
<style>
:root{
  --bg:#e7e8ea;
  --paper:#ffffff;
  --ink:#1c1c1c;
  --text:#3a3a3a;
  --muted:#6b6b6b;
  --orange:#f7a01c;
  --orange-dark:#d98a12;
  --rule:#2a2a2a;
}
*{margin:0;padding:0;box-sizing:border-box}
html,body{width:1200px;height:992px;overflow:hidden;background:var(--bg)}
body{position:relative;font-family:"Roboto",Arial,sans-serif;color:var(--text)}
.piece{position:absolute;background:var(--paper);overflow:hidden}
.band{position:absolute;left:0;right:0;bottom:0;display:flex}
.band .dark{background:var(--ink)}
.band .accent{flex:1;background:var(--orange)}
.abs{position:absolute}

/* wordmark */
.wordmark{position:absolute;display:flex;align-items:center;gap:5px;font-family:"Roboto",Arial,sans-serif;font-weight:700;color:var(--ink);white-space:nowrap;letter-spacing:.02em}
.wordmark .mark-square{background:var(--orange);flex:none}

/* icons */
.icon{width:1em;height:1em;fill:var(--orange);vertical-align:-0.12em;margin-right:.35em}

/* business card */
.card-front{left:103px;top:201px;width:328px;height:187px}
.card-front .wordmark{right:38px;top:56px;font-size:17px}
.card-front .wordmark .mark-square{width:11px;height:11px}
.card-name{left:34px;top:95px;font-family:"Montserrat",Arial,sans-serif;font-weight:600;font-size:13px;color:#2b2b2b;letter-spacing:.01em}
.card-title{left:34px;top:111px;font-size:8px;color:var(--orange)}
.card-rule{left:97px;top:114.5px;width:198px;height:1px;background:var(--rule)}
.card-contacts{left:34px;top:127px;font-size:9.6px;line-height:12.6px;color:#444;font-weight:300}
.card-address{right:33px;top:129px;text-align:right;font-size:9.6px;line-height:11.6px;color:#333;font-weight:300}

.card-back{left:104px;top:413px;width:327px;height:186px;background:linear-gradient(135deg,#8a8a8a 0%,#3e3e3e 35%,#1b1b1b 65%,#0e0e0e 100%)}

/* letterhead */
.letter{top:201px;width:311px;height:398px}
.letter-a{left:459px}
.letter-b{left:786px}
.letter .wordmark{left:31px;top:48px;font-size:11.5px}
.letter .wordmark .mark-square{width:8px;height:8px}
.letter-contacts{left:206px;top:31px;font-size:6.3px;line-height:8.4px;color:#444}
.letter-contacts .gap{height:2.5px}
.letter-body{left:31px;top:121px;width:248px;font-size:5.2px;line-height:6.5px;color:#6a6a6a}
.letter-body p{margin-bottom:6.5px;text-align:justify}
.signoff{left:31px;top:280px;font-size:5px;color:#6a6a6a}
.signer{left:31px;top:305px;font-size:5px;line-height:6.3px;color:#6a6a6a}
.signature{left:31px;top:325px;width:24px;height:22px;background:linear-gradient(135deg,#e4e4e4,#cfcfcf);border-radius:2px}

/* envelope back */
.env-back{left:104px;top:629px;width:349px;height:163px;background:none;overflow:visible}
.env-back svg{position:absolute;left:0;top:0}
.env-back .wordmark{left:50%;transform:translateX(-50%);top:22px;font-size:10px;color:#ffffff}
.env-back .wordmark .mark-square{width:7px;height:7px}

/* envelope front */
.env-front{left:470px;top:629px;width:348px;height:163px}
.env-front .wordmark{left:28px;top:55px;font-size:14px}
.env-front .wordmark .mark-square{width:9px;height:9px}
.env-return{left:25px;top:79px;width:100px;text-align:center;font-size:6.2px;line-height:7.6px;color:#444}
.env-window{left:224px;top:95px;width:99px;height:42px;border-radius:3px;background:linear-gradient(120deg,#e9e9e9,#c9c9c9 60%,#dcdcdc);border:1px solid #d0d0d0}

/* mailing label */
.label{left:845px;top:629px;width:237px;height:160px}
.label-head{left:17px;top:19px;width:203px;height:16px;background:var(--ink);color:#fff;font-size:7.4px;font-weight:500;letter-spacing:.04em;display:flex;align-items:center;justify-content:center}
.label-from{left:17px;top:44px;font-size:8.6px;color:#333}
.label-line{left:17px;width:75px;height:1px;background:#555}
.label .wordmark{left:17px;top:100px;font-size:10.5px;line-height:12px;align-items:flex-start}
.label .wordmark .mark-square{width:7px;height:7px;margin-top:2.5px}
.label-address{left:106px;top:92px;font-size:8.6px;line-height:10.6px;color:#333}
.label-box{left:106px;top:135px;font-size:8.6px;color:#333}
.label-box span{display:inline-block;width:32px;border-bottom:1px solid #444;margin:0 2px}
</style>
</head>
<body>

<svg width="0" height="0" style="position:absolute" aria-hidden="true">
  <symbol id="i-phone" viewBox="0 0 24 24"><path d="M6.6 10.8a15.1 15.1 0 0 0 6.6 6.6l2.2-2.2c.3-.3.7-.4 1-.2 1.1.4 2.3.6 3.6.6.6 0 1 .4 1 1V20c0 .6-.4 1-1 1A17 17 0 0 1 3 4c0-.6.4-1 1-1h3.5c.6 0 1 .4 1 1 0 1.3.2 2.5.6 3.6.1.3 0 .7-.2 1z"/></symbol>
  <symbol id="i-mail" viewBox="0 0 24 24"><path d="M2 5h20v14H2z M2 5l10 7 10-7" /><path d="M3 6l9 6.3L21 6v-.5H3z" fill="#fff"/></symbol>
  <symbol id="i-web" viewBox="0 0 24 24"><circle cx="12" cy="12" r="10"/><path d="M2 12h20M12 2c3 3 3 17 0 20M12 2c-3 3-3 17 0 20" stroke="#fff" stroke-width="1.6" fill="none"/></symbol>
</svg>

<!-- Business card front -->
<section class="piece card-front">
  <div class="wordmark"><span class="mark-square"></span>HARLOW LAW LLC</div>
  <div class="abs card-name">DANA WHITFIELD</div>
  <div class="abs card-title">Founder &amp; CEO</div>
  <div class="abs card-rule"></div>
  <div class="abs card-contacts">
    <div><svg class="icon"><use href="#i-phone"/></svg>(555) 014-2290</div>
    <div><svg class="icon"><use href="#i-mail"/></svg>info@harlowlawllc.com</div>
    <div><svg class="icon"><use href="#i-web"/></svg>www.harlowlawllc.com</div>
  </div>
  <div class="abs card-address">480 Seaview Ave Suite 12,<br>Bayfront,<br>90000 California / USA</div>
  <div class="band" style="height:11px"><div class="dark" style="width:214px"></div><div class="accent"></div></div>
</section>

<!-- Business card back -->
<section class="piece card-back" role="img" aria-label="Card back: dark embossed repeating brand pattern"></section>

<!-- Letterhead first page -->
<section class="piece letter letter-a">
  <div class="wordmark"><span class="mark-square"></span>HARLOW LAW LLC</div>
  <div class="abs letter-contacts">
    <div>Bayfront, St</div>
    <div>90000 California / USA</div>
    <div class="gap"></div>
    <div><svg class="icon"><use href="#i-phone"/></svg>(555) 014-2290</div>
    <div><svg class="icon"><use href="#i-mail"/></svg>info@harlowlawllc.com</div>
    <div><svg class="icon"><use href="#i-web"/></svg>www.harlowlawllc.com</div>
  </div>
  <div class="abs letter-body">
    <p>Dear customer,</p>
    <p>Thank you for reaching out to our office. We have reviewed the documents you provided and prepared a summary of the next steps. Our team will contact you within five business days to arrange a meeting and answer any questions you may have about the process ahead. Please bring photo identification and any letters you have received.</p>
    <p>Please keep this letter with your records. If any details change before our meeting, let us know so we can update your file and adjust the schedule. We value your trust and will keep you informed at every stage of the matter. Calls and emails are answered within one working day.</p>
    <p>Thank you for reaching out to our office. We have reviewed the documents you provided and prepared a summary of the next steps. Our team will contact you within five business days to arrange a meeting and answer any questions you may have about the process ahead. Please bring photo identification and any letters you have received.</p>
    <p>Our fees and terms are set out in the enclosed sheet for your review. Kindly sign and return the copy.</p>
  </div>
  <div class="abs signoff">Yours Sincerely,</div>
  <div class="abs signer">Paul Reyes<br>General Director</div>
  <div class="abs signature" role="img" aria-label="Handwritten signature"></div>
  <div class="band" style="height:9px"><div class="dark" style="width:198px"></div><div class="accent"></div></div>
</section>

<!-- Letterhead second sheet -->
<section class="piece letter letter-b">
  <div class="wordmark"><span class="mark-square"></span>HARLOW LAW LLC</div>
  <div class="abs letter-contacts">
    <div>Bayfront, St</div>
    <div>90000 California / USA</div>
    <div class="gap"></div>
    <div><svg class="icon"><use href="#i-phone"/></svg>(555) 014-2290</div>
    <div><svg class="icon"><use href="#i-mail"/></svg>info@harlowlawllc.com</div>
    <div><svg class="icon"><use href="#i-web"/></svg>www.harlowlawllc.com</div>
  </div>
  <div class="abs letter-body">
    <p>Dear customer,</p>
    <p>Thank you for reaching out to our office. We have reviewed the documents you provided and prepared a summary of the next steps. Our team will contact you within five business days to arrange a meeting and answer any questions you may have about the process ahead. Please bring photo identification and any letters you have received.</p>
    <p>Please keep this letter with your records. If any details change before our meeting, let us know so we can update your file and adjust the schedule. We value your trust and will keep you informed at every stage of the matter. Calls and emails are answered within one working day.</p>
    <p>Thank you for reaching out to our office. We have reviewed the documents you provided and prepared a summary of the next steps. Our team will contact you within five business days to arrange a meeting and answer any questions you may have about the process ahead. Please bring photo identification and any letters you have received.</p>
    <p>Our fees and terms are set out in the enclosed sheet for your review. Kindly sign and return the copy.</p>
  </div>
  <div class="abs signoff">Yours Sincerely,</div>
  <div class="abs signer">Paul Reyes<br>General Director</div>
  <div class="abs signature" role="img" aria-label="Handwritten signature"></div>
  <div class="band" style="height:9px"><div class="dark" style="width:198px"></div><div class="accent"></div></div>
</section>

<!-- Envelope back -->
<section class="piece env-back">
  <svg width="349" height="163" viewBox="0 0 349 163" aria-hidden="true">
    <rect x="0" y="0" width="349" height="163" fill="#ffffff"/>
    <path d="M10 30 L4 160 M339 30 L345 160" stroke="#d6d6d6" stroke-width="1" fill="none"/>
    <path d="M0 0 H349 L329 52 Q325 60 314 60 H35 Q24 60 20 52 Z" fill="#1c1c1c"/>
  </svg>
  <div class="wordmark"><span class="mark-square"></span>HARLOW LAW LLC</div>
</section>

<!-- Envelope front -->
<section class="piece env-front">
  <div class="wordmark"><span class="mark-square"></span>HARLOW LAW LLC</div>
  <div class="abs env-return">88 Mill Street, Suite 4<br>Easton, MA 02000</div>
  <div class="abs env-window"></div>
  <div class="band" style="height:11px"><div class="dark" style="width:224px"></div><div class="accent"></div></div>
</section>

<!-- Mailing label -->
<section class="piece label">
  <div class="abs label-head">MAILING LABEL</div>
  <div class="abs label-from">FROM</div>
  <div class="abs label-line" style="top:62px"></div>
  <div class="abs label-line" style="top:72px"></div>
  <div class="abs label-line" style="top:82px"></div>
  <div class="wordmark"><span class="mark-square"></span><span>HARLOW<br>LAW LLC</span></div>
  <div class="abs label-address">480 Seaview Ave Suite 12,<br>Bayfront,<br>90000 California / USA</div>
  <div class="abs label-box">BOX<span></span>OF<span></span></div>
</section>

</body>
</html>
```